Business Card Design for Training Business

Clear Path Coaching is a new business that delivers training and other services with a focus on topics related to mental health and wellbeing, for example, Wellmind Response Course, Resilience etc. We have a strong focus on evidence-based psychology and neuroscience. I have a logo which I will upload with the brief, so please consider colours that work well with the logo.
Target Market(s)
Adults, workplaces (particularly government and not-for-profits)
Industry/Entity Type
Business
Contact Information for Business Card
Head Strong TrainingSamantha SellwoodDirector0438 770 850sam@headstrongtraining.com.auwww.headstrongtraining.com.au

```html
<!DOCTYPE html>
<html lang="en">
<head>
<meta charset="utf-8">
<title>Clear Path Coaching — Business Card</title>
<link rel="stylesheet" href="https://fonts.googleapis.com/css2?family=Open+Sans:wght@300;400;700&display=swap">
<style>
  :root {
    --page-bg: #e8e4e0;
    --card-brown-light: #8b7b75;
    --card-brown-dark: #6c5d58;
    --teal: #2ec4c9;
    --line-white: #e9ecec;
    --text-white: #ffffff;
    --text-soft: #e3dcd8;
    --logo-grey: #d4cdc9;
  }
  * { margin: 0; padding: 0; box-sizing: border-box; }
  html, body {
    width: 1200px;
    height: 1022px;
    overflow: hidden;
    background: var(--page-bg);
    font-family: "Open Sans", Arial, sans-serif;
  }
  .card {
    position: absolute;
    left: 120px;
    top: 218px;
    width: 960px;
    height: 587px;
    border-radius: 18px;
    overflow: hidden;
    background: linear-gradient(160deg, var(--card-brown-light) 0%, var(--card-brown-dark) 100%);
    box-shadow: 0 10px 30px rgba(60, 45, 40, 0.25);
  }
  .card-bands {
    position: absolute;
    inset: 0;
    width: 960px;
    height: 587px;
  }
  .brand {
    position: absolute;
    left: 112px;
    top: 266px;
    display: flex;
    align-items: center;
    gap: 16px;
  }
  .brand-dot {
    width: 52px;
    height: 52px;
    border-radius: 50%;
    border: 3px solid var(--teal);
    flex: none;
  }
  .brand-name {
    font-weight: 300;
    font-size: 30px;
    letter-spacing: 1.5px;
    color: var(--logo-grey);
    white-space: nowrap;
  }
  .divider {
    position: absolute;
    left: 498px;
    top: 160px;
    width: 2px;
    height: 270px;
    background: var(--line-white);
    opacity: 0.85;
  }
  .contact {
    position: absolute;
    left: 524px;
    top: 172px;
    color: var(--text-white);
  }
  .contact-name {
    font-weight: 700;
    font-size: 34px;
    line-height: 1.15;
    white-space: nowrap;
  }
  .contact-role {
    font-weight: 400;
    font-size: 20px;
    color: var(--teal);
    margin-bottom: 20px;
  }
  .contact-list { list-style: none; }
  .contact-item {
    display: flex;
    align-items: center;
    gap: 10px;
    font-size: 18px;
    line-height: 1.65;
    color: var(--text-soft);
    white-space: nowrap;
  }
  .contact-icon { width: 17px; height: 17px; flex: none; }
</style>
</head>
<body>
  <div class="card">
    <svg class="card-bands" viewBox="0 0 960 587" aria-hidden="true">
      <path d="M0,0 L30,0 Q55,330 170,587 L0,587 Z" fill="var(--teal)"/>
      <path d="M30,0 Q55,330 170,587" fill="none" stroke="var(--line-white)" stroke-width="6"/>
      <path d="M960,0 L840,0 Q905,250 935,587 L960,587 Z" fill="var(--teal)"/>
      <path d="M840,0 Q905,250 935,587" fill="none" stroke="var(--line-white)" stroke-width="6"/>
    </svg>

    <div class="brand">
      <span class="brand-dot"></span>
      <span class="brand-name">Clear Path Coaching</span>
    </div>

    <div class="divider"></div>

    <div class="contact">
      <div class="contact-name">Rebecca Tanfield</div>
      <div class="contact-role">Director</div>
      <ul class="contact-list">
        <li class="contact-item">
          <svg class="contact-icon" viewBox="0 0 24 24"><path fill="var(--teal)" d="M6.6 10.8a15.1 15.1 0 0 0 6.6 6.6l2.2-2.2c.3-.3.7-.4 1-.2 1.1.4 2.3.6 3.6.6.6 0 1 .4 1 1V20c0 .6-.4 1-1 1A17 17 0 0 1 3 4c0-.6.4-1 1-1h3.5c.6 0 1 .4 1 1 0 1.3.2 2.5.6 3.6.1.3 0 .7-.2 1z"/></svg>
          <span>0491 362 517</span>
        </li>
        <li class="contact-item">
          <svg class="contact-icon" viewBox="0 0 24 24"><rect x="2" y="5" width="20" height="14" rx="2" fill="none" stroke="var(--teal)" stroke-width="2.4"/><path d="M3 6l9 7 9-7" fill="none" stroke="var(--teal)" stroke-width="2.4"/></svg>
          <span>bec@clearpathcoaching.example.au</span>
        </li>
        <li class="contact-item">
          <svg class="contact-icon" viewBox="0 0 24 24"><circle cx="12" cy="12" r="10" fill="none" stroke="var(--teal)" stroke-width="2.4"/><path d="M2 12h20M12 2c3 3 3 17 0 20M12 2c-3 3-3 17 0 20" fill="none" stroke="var(--teal)" stroke-width="1.8"/></svg>
          <span>www.clearpathcoaching.example.au</span>
        </li>
      </ul>
    </div>
  </div>
</body>
</html>
```